Website for Swedish wellness company "Heartmeadow"

We need a website for our Swedish wellness company. The name is "Heartmeadow" . The company is all about sustainablility for our body, soul and planet. We work with coaching, yoga, massage, healthy food, retreats(sports, excercise, sufing), healing and inspirational talks. We are convinced that personal sustainability and a strong spiritual connection to yourself will lead to planetary sustainability. Our customers are both companies and consumers from all over the world. The final design should be clean/simple and you should get a feeling of community, happiness, warmth, connection,, joy, spirituality but still a professional touch.Just got a logo from Pixel Harbor and are very happy with it;-)
Updates

Sorry I was too enthusiastic posting this project. Of course I will give you some text as well för the different pages! I will see to that it is finished by friday so if you want to wait with your submissions please do! Best regards Maria

Target Market(s)

Businesses and consumers

Industry/Entity Type

Health And Wellness

Number of Pages Required

5+ page

Font styles to use
Sans Serif

Colors
33a6d7
00a990
b7a5cd

Requirements
Must have
• Idea about pages:
• I am not sure how many pages I get for the price, but 5 would be nice to start with.
• Not sure what write ups is;-)
• But title of the pages could be:
• Landing page
• About us
• Services
• Retreats
• Contact us
Nice to have
• A clean and professional website but with some heart and soul in it. Because we Would love colours that harmonize with our logo, but other ideas are welcome!

```html
<!DOCTYPE html>
<html lang="en">
<head>
<meta charset="utf-8">
<title>Heartmeadow – Swedish Wellness</title>
<link href="https://fonts.googleapis.com/css2?family=Prata&family=Poppins:wght@400;500;600&display=swap" rel="stylesheet">
<style>
:root{
  --navy:#14284b;
  --teal:#149a84;
  --teal-dark:#0d7f6c;
  --text:#4a4a4a;
  --cream:#fbf5e6;
  --footer:#161616;
  --white:#ffffff;
}
*{box-sizing:border-box;margin:0;padding:0}
html,body{width:1200px;height:4922px;overflow:hidden}
body{font-family:"Poppins",sans-serif;color:var(--text);background:var(--white);position:relative}
section{position:absolute;left:0;width:1200px;overflow:hidden}
.abs{position:absolute}
p.small{font-size:13.5px;line-height:33px}
.btn-outline{display:inline-block;border:2px solid var(--teal);color:var(--teal);font-family:"Prata",serif;font-size:16px;padding:8px 24px;background:#fff}
.rule{width:70px;height:3px;background:#fff;margin:22px auto 0}
.section-title{font-family:"Prata",serif;font-weight:400;font-size:44px;text-align:center;color:#fff}

/* hero */
.hero{top:0;height:812px}
.hero-photo{position:absolute;inset:0;background:linear-gradient(100deg,#7da48f 0%,#c9d9d6 30%,#d7e6ea 55%,#7aa9b0 100%)}
.header{position:absolute;top:0;left:0;width:1200px;height:150px}
.brand{position:absolute;left:142px;top:22px;display:flex;flex-direction:column;align-items:center}
.brand .mark{width:66px;height:66px;border-radius:50%;background:#2fb3a2}
.brand .name{font-family:"Prata",serif;font-size:25px;color:var(--navy);margin-top:10px;letter-spacing:1px}
.call{position:absolute;left:588px;top:40px;display:flex;align-items:center;gap:14px;color:var(--navy)}
.call .icon{width:34px;height:34px;border-radius:50%;background:var(--navy);display:flex;align-items:center;justify-content:center}
.call small{display:block;font-size:14px;line-height:16px}
.call b{font-family:"Prata",serif;font-weight:400;font-size:20px;line-height:24px}
.book{position:absolute;left:817px;top:42px;border:2px solid var(--navy);border-radius:22px;padding:6px 20px;font-family:"Prata",serif;font-size:16px;color:var(--navy);background:rgba(255,255,255,.6)}
.nav{position:absolute;left:494px;top:110px;display:flex;gap:34px;font-family:"Prata",serif;font-size:18px;color:var(--navy)}
.slide-card{position:absolute;left:602px;top:296px;width:455px;height:272px;background:rgba(255,255,255,.8);border-radius:24px;padding:24px 30px}
.slide-card h1{font-family:"Prata",serif;font-weight:400;font-size:44px;color:var(--navy)}
.slide-card p{font-size:15px;line-height:30px;margin-top:10px;color:#444}
.slide-card .pill{display:inline-block;margin-top:18px;border:2px solid var(--navy);border-radius:22px;padding:6px 20px;font-family:"Prata",serif;font-size:16px;color:var(--navy)}
.arrow{position:absolute;top:433px;width:32px;height:32px;border-radius:50%;background:#2a3b4a;display:flex;align-items:center;justify-content:center}

/* about */
.about{top:740px;height:720px}
.about h2{position:absolute;left:144px;top:130px;font-family:"Prata",serif;font-weight:400;font-size:42px;color:var(--navy);white-space:nowrap}
.about h2 span{color:var(--teal)}
.about .copy{position:absolute;left:144px;top:210px;width:390px}
.hex{position:absolute;width:222px;height:256px}
.hex .inner{position:absolute;top:30px;left:0;width:222px;text-align:center;padding:0 26px}
.hex .ic{width:68px;height:68px;border-radius:50%;border:3px solid #2fb3a2;margin:0 auto}
.hex h4{font-family:"Prata",serif;font-weight:400;font-size:20px;line-height:28px;color:var(--navy);margin-top:8px}
.hex p{font-size:11.5px;line-height:21px;margin-top:2px}

/* services */
.services{top:1420px;height:850px;background:linear-gradient(135deg,#1a9a66 0%,#169685 50%,#15a08b 100%)}
.services .section-title{margin-top:110px}
.svc{position:absolute;width:251px;background:#fff;box-shadow:0 4px 12px rgba(0,0,0,.2);text-align:center}
.svc .photo{height:190px}
.svc .badge{width:48px;height:48px;border-radius:50%;background:var(--teal);border:3px solid #fff;margin:-24px auto 0;position:relative}
.svc h3{font-family:"Prata",serif;font-weight:400;font-size:23px;color:#222;margin-top:6px}
.svc p{font-size:12.5px;line-height:26px;padding:8px 14px 20px}

/* retreats */
.retreats{top:2230px;height:650px;background:var(--cream)}
.retreat-photo{position:absolute;left:0;top:0;width:560px;height:650px;background:radial-gradient(circle at 75% 35%,#fff6cf 0%,#e9b868 25%,#a77c5c 55%,#4b4a55 100%)}
.retreats h2{position:absolute;left:615px;top:130px;font-family:"Prata",serif;font-weight:400;font-size:44px;color:var(--navy)}
.retreats .copy{position:absolute;left:615px;top:210px;width:440px}

/* blog */
.blog{top:2850px;height:880px;background:linear-gradient(180deg,#3b96cf 0%,#3a9ad4 60%,#3f9fd7 100%)}
.blog .section-title{margin-top:140px}
.post{position:absolute;width:280px}
.post .photo{height:200px;position:relative}
.post .date{position:absolute;left:12px;top:14px;background:var(--teal);color:#fff;font-family:"Prata",serif;font-style:italic;font-size:13px;line-height:17px;padding:4px 8px}
.post .body{background:#fff;margin:-8px 12px 0;padding:18px 20px;text-align:center;position:relative}
.post h4{font-weight:400;font-size:16px;line-height:27px;color:var(--teal)}
.post p{font-size:12.5px;line-height:24px;margin-top:10px}

/* testimonials */
.testimonials{top:3707px;height:600px;background:#fff}
.testimonials h2{text-align:center;font-family:"Prata",serif;font-weight:400;font-size:44px;color:#222;margin-top:50px}
.testimonials .rule{background:var(--teal)}
.quote{position:absolute;width:275px;text-align:center}
.quote .bubble{background:#fff;box-shadow:0 2px 12px rgba(0,0,0,.12);border-radius:6px;padding:70px 22px 26px;font-size:12.5px;line-height:23px}
.quote.active .bubble{border:1px solid var(--teal)}
.quote .avatar{position:absolute;left:50%;top:-40px;margin-left:-42px;width:84px;height:84px;border-radius:50%;border:3px solid var(--teal);background:linear-gradient(160deg,#b07a60,#4b2f2a)}
.quote .who{margin-top:34px;font-size:15px;line-height:26px;color:#222}
.quote .stars{color:var(--teal);letter-spacing:4px;font-size:16px;margin-top:6px}

/* footer */
.footer{top:4280px;height:642px;background:var(--footer);color:#fff}
.footer h5{position:absolute;top:126px;font-family:"Prata",serif;font-weight:400;font-size:24px}
.footer .u{position:absolute;top:173px;width:60px;height:2px;background:#fff}
.field{position:absolute;left:147px;width:362px;height:34px;border:1px solid #ddd;font-size:11px;padding:8px 10px}
.submit{position:absolute;left:147px;top:435px;width:176px;height:38px;background:var(--teal);font-family:"Prata",serif;font-size:17px;text-align:center;line-height:38px}
.ci{position:absolute;left:568px;display:flex;gap:16px;font-size:13px;line-height:22px}
.ci .ico{width:30px;height:30px;border-radius:50%;border:2px solid #fff;flex:none;display:flex;align-items:center;justify-content:center}
.social{position:absolute;left:569px;top:427px;display:flex;gap:10px}
.social span{width:30px;height:30px;border-radius:50%;border:2px solid #fff}
.links{position:absolute;left:905px;top:210px;font-size:13px;line-height:28px;list-style:none}
.copyright{position:absolute;top:582px;width:1200px;text-align:center;font-size:13px}
.footer .line{position:absolute;left:144px;top:553px;width:912px;height:1px;background:#2d2d2d}
</style>
</head>
<body>

<section class="hero">
  <div class="hero-photo" role="img" aria-label="Woman meditating cross-legged on a wooden jetty by a misty mountain lake"></div>
  <header class="header">
    <div class="brand"><div class="mark"></div><div class="name">HEARTMEADOW</div></div>
    <div class="call">
      <div class="icon"><svg width="16" height="16" viewBox="0 0 24 24"><path fill="#fff" d="M6.6 10.8a15 15 0 0 0 6.6 6.6l2.2-2.2c.3-.3.7-.4 1-.2 1.1.4 2.3.6 3.6.6.6 0 1 .4 1 1V20c0 .6-.4 1-1 1A17 17 0 0 1 3 4c0-.6.4-1 1-1h3.5c.6 0 1 .4 1 1 0 1.3.2 2.5.6 3.6.1.3 0 .7-.2 1z"/></svg></div>
      <div><small>Call Us :</small><b>555 0140 2626</b></div>
    </div>
    <div class="book">✎ Book a Consultation</div>
    <nav class="nav"><span>Home</span><span>About us</span><span>Our Services</span><span>Retreats</span><span>Contact us</span></nav>
  </header>
  <div class="slide-card">
    <h1>Swedish Wellness</h1>
    <p>Nemo enim ipsam voluptatem quia voluptas sit aspernatur aut odit aut fugit, sed quia consequuntur magni dolores eos qui ratione voluptatem</p>
    <span class="pill">make an appointment</span>
  </div>
  <div class="arrow" style="left:55px"><svg width="12" height="12" viewBox="0 0 12 12"><path d="M8 1 3 6l5 5" stroke="#fff" stroke-width="2" fill="none"/></svg></div>
  <div class="arrow" style="left:1110px"><svg width="12" height="12" viewBox="0 0 12 12"><path d="M4 1l5 5-5 5" stroke="#fff" stroke-width="2" fill="none"/></svg></div>
  <svg class="abs" style="left:0;top:720px" width="1200" height="92" viewBox="0 0 1200 92"><path d="M0 50 Q600 -20 1200 60 L1200 92 L0 92Z" fill="#fff"/><path d="M40 92 Q600 10 1160 88" stroke="#2fb3a2" stroke-width="3" fill="none"/></svg>
</section>

<section class="about">
  <h2>About <span>Heartmeadow</span></h2>
  <div class="copy">
    <p class="small">Sed ut perspiciatis unde omnis iste natus error sit voluptatem accusantium doloremque laudantium, totam rem aperiam, eaque ipsa quae ab illo inventore veritatis et quasi architecto beatae vitae dicta sunt explicabo. Nemo enim ipsam voluptatem quia voluptas sit aspernatur aut odit aut fugit, sed quia consequuntur magni dolores eos qui ratione</p>
    <div style="margin-top:36px"><span class="btn-outline">Read More</span></div>
  </div>
  <svg class="abs" style="left:598px;top:108px" width="460" height="470" viewBox="0 0 460 470">
    <g fill="#fff" stroke="#bfe3de" stroke-width="2">
      <polygon points="111,2 221,66 221,194 111,258 1,194 1,66"/>
      <polygon points="347,2 457,66 457,194 347,258 237,194 237,66"/>
      <polygon points="229,206 339,270 339,398 229,462 119,398 119,270"/>
    </g>
  </svg>
  <div class="hex" style="left:598px;top:108px"><div class="inner"><div class="ic"></div><h4>BODY</h4><p>Sed ut perspiciatis unde omnis iste natus error sit santium doloremque</p></div></div>
  <div class="hex" style="left:834px;top:108px"><div class="inner"><div class="ic"></div><h4>SOUL</h4><p>Sed ut perspiciatis unde omnis iste natus error sit santium doloremque</p></div></div>
  <div class="hex" style="left:716px;top:312px"><div class="inner"><div class="ic"></div><h4>PLANET</h4><p>Sed ut perspiciatis unde omnis iste natus error sit santium doloremque</p></div></div>
</section>

<section class="services">
  <svg class="abs" style="left:0;top:0" width="1200" height="60" viewBox="0 0 1200 60"><path d="M0 0 H1200 V20 Q900 50 600 25 Q300 0 0 30Z" fill="#fff"/></svg>
  <h2 class="section-title">Our Services</h2>
  <div class="rule"></div>
  <div class="svc" style="left:72px;top:270px"><div class="photo" style="background:linear-gradient(160deg,#c8c3b8,#6c6560)" role="img" aria-label="Coaching session in an office"></div><div class="badge"></div><h3>Coaching</h3><p>Nemo enim ipsam voluptatem quia voluptas sit aspernatur aut odit aut fugit, sed quia consequuntur magni dolores eos qui ratione</p></div>
  <div class="svc" style="left:344px;top:302px"><div class="photo" style="background:linear-gradient(180deg,#d9e2d6,#7c9f6e)" role="img" aria-label="Woman practising yoga outdoors"></div><div class="badge"></div><h3>Yoga</h3><p>Nemo enim ipsam voluptatem quia voluptas sit aspernatur aut odit aut fugit, sed quia consequuntur magni dolores eos qui ratione</p></div>
  <div class="svc" style="left:616px;top:270px"><div class="photo" style="background:linear-gradient(160deg,#6a3b22,#e4b08b)" role="img" aria-label="Relaxing spa massage"></div><div class="badge"></div><h3>Massage</h3><p>Nemo enim ipsam voluptatem quia voluptas sit aspernatur aut odit aut fugit, sed quia consequuntur magni dolores eos qui ratione</p></div>
  <div class="svc" style="left:888px;top:302px"><div class="photo" style="background:linear-gradient(160deg,#cfe1ea,#c99a78)" role="img" aria-label="Woman enjoying a healthy meal"></div><div class="badge"></div><h3>Healthy food</h3><p>Nemo enim ipsam voluptatem quia voluptas sit aspernatur aut odit aut fugit, sed quia consequuntur magni dolores eos qui ratione</p></div>
</section>

<section class="retreats">
  <div class="retreat-photo" role="img" aria-label="Balanced stacked stones at sunset labelled body, mind, soul and spirit"></div>
  <svg class="abs" style="left:0;top:0" width="1200" height="50" viewBox="0 0 1200 50"><path d="M0 0 H1200 V10 Q900 40 600 15 Q300 -5 0 25Z" fill="#169685"/></svg>
  <h2>Retreats</h2>
  <div class="copy">
    <p class="small">Sed ut perspiciatis unde omnis iste natus error sit voluptatem accusantium doloremque laudantium, totam rem aperiam, eaque ipsa quae ab illo inventore veritatis et quasi architecto beatae vitae dicta sunt explicabo. Nemo enim ipsam voluptatem quia voluptas sit aspernatur aut odit aut fugit, sed quia consequuntur magni dolores eos qui ratione</p>
    <div style="margin-top:36px"><span class="btn-outline">Read More</span></div>
  </div>
</section>

<section class="blog">
  <svg class="abs" style="left:0;top:0" width="1200" height="60" viewBox="0 0 1200 60"><path d="M0 0 H1200 V5 Q900 0 600 30 Q300 60 0 40Z" fill="#fbf5e6"/></svg>
  <h2 class="section-title">Latest Blog</h2>
  <div class="rule"></div>
  <div class="post" style="left:132px;top:288px"><div class="photo" style="background:linear-gradient(160deg,#d8d0c6,#8a6d5c)" role="img" aria-label="Couple preparing healthy food in a kitchen"><span class="date">Oct 01<br>2019</span></div><div class="body"><h4>Sed ut perspiciatis unde omnis iste natus</h4><p>Sed ut perspiciatis unde omnis iste natus sit voluptatem accusantium domque laudantium, totam</p></div></div>
  <div class="post" style="left:434px;top:288px;width:328px"><div class="photo" style="background:linear-gradient(160deg,#8a5a3c,#4a7fa0)" role="img" aria-label="Group yoga class stretching on mats"><span class="date">Oct 01<br>2019</span></div><div class="body"><h4>Sed ut perspiciatis unde omnis iste natus</h4><p>Sed ut perspiciatis unde omnis iste natus sit voluptatem accusantium domque laudantium, totam</p></div></div>
  <div class="post" style="left:790px;top:288px"><div class="photo" style="background:linear-gradient(160deg,#b58a6e,#f0d6c2)" role="img" aria-label="Woman receiving a back massage"><span class="date">Oct 01<br>2019</span></div><div class="body"><h4>Sed ut perspiciatis unde omnis iste natus</h4><p>Sed ut perspiciatis unde omnis iste natus sit voluptatem accusantium domque laudantium, totam</p></div></div>
  <svg class="abs" style="left:0;top:800px" width="1200" height="80" viewBox="0 0 1200 80"><path d="M0 60 Q300 80 600 50 Q900 20 1200 35 V80 H0Z" fill="#fff"/></svg>
</section>

<section class="testimonials">
  <h2>Testimonials</h2>
  <div class="rule"></div>
  <div class="quote" style="left:144px;top:230px"><div class="bubble">Sed ut perspiciatis unde omnis iste natus error sit voluptatem accantium doloremque laudantium, totam rem aperiam, eaque ipsa</div><div class="avatar" role="img" aria-label="Customer portrait"></div><div class="who">Omar Lindqvist<br>Quis autem vel eum</div><div class="stars">★★★★★</div></div>
  <div class="quote active" style="left:462px;top:230px"><div class="bubble">Sed ut perspiciatis unde omnis iste natus error sit voluptatem accantium doloremque laudantium, totam rem aperiam, eaque ipsa</div><div class="avatar" role="img" aria-label="Customer portrait"></div><div class="who">Omar Lindqvist<br>Quis autem vel eum</div><div class="stars">★★★★★</div></div>
  <div class="quote" style="left:780px;top:230px"><div class="bubble">Sed ut perspiciatis unde omnis iste natus error sit voluptatem accantium doloremque laudantium, totam rem aperiam, eaque ipsa</div><div class="avatar" role="img" aria-label="Customer portrait" style="background:linear-gradient(160deg,#6a8fb8,#2a3d5c)"></div><div class="who">Omar Lindqvist<br>Quis autem vel eum</div><div class="stars">★★★★★</div></div>
</section>

<section class="footer">
  <svg class="abs" style="left:0;top:0" width="1200" height="70" viewBox="0 0 1200 70"><path d="M0 0 H1200 V20 Q600 90 0 20Z" fill="#fff"/><path d="M40 20 Q600 75 1160 20" stroke="#2fb3a2" stroke-width="3" fill="none"/></svg>
  <h5 style="left:145px">Book a Consultation</h5><div class="u" style="left:147px"></div>
  <h5 style="left:568px">Contact Us</h5><div class="u" style="left:568px"></div>
  <h5 style="left:905px">Quick Links</h5><div class="u" style="left:905px"></div>
  <div class="field" style="top:225px">First Name</div>
  <div class="field" style="top:270px">Email Address</div>
  <div class="field" style="top:315px">Phone Number</div>
  <div class="field" style="top:360px;height:60px">Message :</div>
  <div class="submit">SUBMIT</div>
  <div class="ci" style="top:215px"><span class="ico"><svg width="12" height="14" viewBox="0 0 12 16"><path d="M6 0a6 6 0 0 1 6 6c0 4-6 10-6 10S0 10 0 6a6 6 0 0 1 6-6z" fill="#fff"/><circle cx="6" cy="6" r="2" fill="#161616"/></svg></span><span>Heartmeadow<br>42 Linden Grove, Suite 12<br>Brookfield, Ohio 45010</span></div>
  <div class="ci" style="top:300px"><span class="ico"><svg width="13" height="13" viewBox="0 0 24 24"><path fill="#fff" d="M6.6 10.8a15 15 0 0 0 6.6 6.6l2.2-2.2c.3-.3.7-.4 1-.2 1.1.4 2.3.6 3.6.6.6 0 1 .4 1 1V20c0 .6-.4 1-1 1A17 17 0 0 1 3 4c0-.6.4-1 1-1h3.5c.6 0 1 .4 1 1 0 1.3.2 2.5.6 3.6.1.3 0 .7-.2 1z"/></svg></span><span>Phone:<br>555 0140 2626</span></div>
  <div class="ci" style="top:357px"><span class="ico"><svg width="13" height="10" viewBox="0 0 14 10"><rect x=".5" y=".5" width="13" height="9" fill="none" stroke="#fff"/><path d="M.5.5 7 6 13.5.5" fill="none" stroke="#fff"/></svg></span><span>Email:<br>hello@heartmeadow.com</span></div>
  <div class="social"><span></span><span></span><span></span></div>
  <ul class="links"><li>Home</li><li>About us</li><li>Services</li><li>Retreats</li><li>Contact us</li></ul>
  <div class="line"></div>
  <div class="copyright">© Copyright 2019 Heartmeadow . All Rights Reserved.</div>
</section>

</body>
</html>
```